GlassHaven Artbook for Okanagan Region, British Columbia

Creating an art book: GlassHaven, for the Okanagan Wine Region in British Columbia, Canada. Would like smart, modern, clean and linear...cool, sexy urban, not ugly boring suburban... I need a cover that appeals to the wino in all of us! Title: GlassHaven -Marla Dovicki
Updates
Thank you all kindly for your efforts. I have added some files so that you can get a sense of my aesthetic...it's never easy trying to figure it out, is it? I will hopefully have dimensions of book soon...cheers, Marla
would anyone please design a giant wine bottle with the wine label that looks like a label but says glasshaven...just curious to see if it works as a design or not...thank you.
Target Market(s)
Designing this wine art book of quotes to wineries in Okanagan BC. Buyer is wine lover and tourist ready to spend his vacation bucks on this wonderful book!
Look and feel

```html
<!DOCTYPE html>
<html lang="en">
<head>
<meta charset="utf-8">
<title>GlassHaven — Cover</title>
<link rel="stylesheet" href="https://fonts.googleapis.com/css2?family=Antonio:wght@200;300&display=swap">
<style>
  :root {
    --page: #ffffff;
    --cover: #e4e4e2;
    --tone-dark: #2b2b2b;
    --tone-red: #a80f15;
    --tone-light: #e4e4e2;
    --title: #ffffff;
    --author: #2e2e2e;
  }
  html, body {
    margin: 0;
    padding: 0;
    width: 1200px;
    height: 1000px;
    overflow: hidden;
    background: var(--page);
  }
  .canvas { display: block; width: 1200px; height: 1000px; }
  .cover-bg { fill: var(--cover); }
  .artwork { fill: url(#artwork-tones); }
  .title {
    font-family: "Antonio", "Arial Narrow", sans-serif;
    font-weight: 200;
    font-size: 40px;
    letter-spacing: 4px;
    fill: var(--title);
  }
  .author {
    font-family: "Antonio", "Arial Narrow", sans-serif;
    font-weight: 300;
    font-size: 19px;
    letter-spacing: 1.6px;
    fill: var(--author);
  }
</style>
</head>
<body>
<svg class="canvas" viewBox="0 0 1200 1000" xmlns="http://www.w3.org/2000/svg">
  <defs>
    <linearGradient id="artwork-tones" x1="0" y1="0" x2="0" y2="1">
      <stop offset="0" stop-color="var(--tone-dark)"/>
      <stop offset="0.22" stop-color="var(--tone-dark)"/>
      <stop offset="0.4" stop-color="var(--tone-red)"/>
      <stop offset="0.58" stop-color="var(--tone-red)"/>
      <stop offset="0.82" stop-color="var(--tone-light)"/>
      <stop offset="1" stop-color="var(--tone-light)"/>
    </linearGradient>
  </defs>

  <g class="cover">
    <rect class="cover-bg" x="365" y="156" width="471" height="653"/>
    <rect class="artwork" x="365" y="156" width="471" height="653"
          role="img" aria-label="Illustration of three tilted wine bottles in black, red and white on a light grey ground"/>

    <text class="title" x="404" y="490">GLASSHAVEN</text>
    <text class="author" x="672" y="759">MARLA DOVICKI</text>
  </g>
</svg>
</body>
</html>
```